Velk Consulting -New consulting business in architecture, urban planning, and real estate development

We need a stationery design, including logo, business cards, etc, work for a new consulting business that works in the world of architectural, urban planning and real estate development.

The name of the company is "Velk Consulting". Velk is my last name but it of course also has the meaning 'cool' and 'hip'.

Target Market(s)

The business will provide boutique consulting services to high end clients that may include property developers, cities, etc.

Industry/Entity Type

Consultant

Contact Information for Business Card

VELK Consulting
First Name Last Name
Title
Phone number
Address
Website
Optional: Twitter handle

Logo Text

VELK Consulting

Font styles to use
Sans Serif

Colors

Designer to choose colors to be used in the design.

Requirements
Must have
• Simple design
• Easy to read font
• Modern
• Elegance
• Nice font that can be used for future reports, letters, etc.
• Good colour scheme that allows for the elegance to come through
Should not have
• Complex design ideas
• Complex logos
• Not a corporate feel and look

```html
<!DOCTYPE html>
<html lang="en">
<head>
<meta charset="utf-8">
<title>Velk Consulting – Letterhead</title>
<link href="https://fonts.googleapis.com/css2?family=Roboto:wght@400;500;700&family=Montserrat:wght@500;700&display=swap" rel="stylesheet">
<style>
  :root {
    --bg: #e6e6e7;
    --paper: #f3f3f4;
    --gold: #a68a2c;
    --gold-light: #b89a3e;
    --ink: #3a3a3c;
    --ink-soft: #6d6d70;
    --footer-ink: #1e1e1e;
    --rule: #9a9a9a;
  }
  * { box-sizing: border-box; margin: 0; padding: 0; }
  html, body { width: 1200px; height: 1179px; overflow: hidden; }
  body {
    background: var(--bg);
    font-family: "Roboto", Arial, sans-serif;
    color: var(--ink);
  }
  .letterhead {
    position: absolute;
    left: 200px;
    top: 24px;
    width: 800px;
    height: 1130px;
    background: var(--paper);
    box-shadow: 0 2px 6px rgba(0,0,0,0.12);
  }
  .header-band {
    position: absolute;
    left: 0; top: 0;
    width: 100%;
    height: 131px;
    background: linear-gradient(90deg, var(--gold) 0%, var(--gold-light) 50%, var(--gold) 100%);
  }
  .brand {
    position: absolute;
    left: 0; top: 0;
    width: 100%;
    height: 131px;
    display: flex;
    align-items: center;
    justify-content: center;
    color: #ffffff;
    font-family: "Roboto", Arial, sans-serif;
    font-weight: 500;
    font-size: 30px;
    letter-spacing: 3px;
  }
  .recipient {
    position: absolute;
    left: 76px;
    top: 280px;
    font-size: 15px;
    line-height: 18.5px;
    letter-spacing: 0.4px;
  }
  .recipient .name, .recipient .title { font-weight: 700; color: var(--ink); }
  .recipient .line { color: var(--ink-soft); }
  .date {
    position: absolute;
    right: 74px;
    top: 337px;
    font-size: 15px;
    letter-spacing: 0.6px;
    color: var(--ink-soft);
  }
  .body-copy {
    position: absolute;
    left: 60px;
    top: 440px;
    width: 680px;
    font-size: 12px;
    line-height: 24px;
    letter-spacing: 0.3px;
    color: var(--ink-soft);
    text-align: justify;
  }
  .body-copy p { text-indent: 13px; margin-bottom: 24px; }
  .footer {
    position: absolute;
    left: 0;
    top: 1020px;
    width: 100%;
    font-family: "Montserrat", Arial, sans-serif;
    font-size: 11px;
    font-weight: 500;
    color: var(--footer-ink);
    text-align: center;
  }
  .footer .address strong { font-weight: 700; }
  .contact-row {
    margin-top: 10px;
    display: flex;
    justify-content: center;
    align-items: center;
  }
  .contact-item {
    display: flex;
    align-items: center;
    gap: 6px;
    padding: 0 11px;
  }
  .contact-item + .contact-item { border-left: 1px solid var(--rule); }
  .contact-item svg { width: 13px; height: 13px; }
</style>
</head>
<body>
  <main class="letterhead">
    <div class="header-band" role="img" aria-label="Gold band with ornamental mandala pattern"></div>
    <div class="brand">VELK Consulting</div>

    <address class="recipient" style="font-style: normal;">
      <div class="name">MR. Daniel HOLLOWAY</div>
      <div class="title">Managing Director</div>
      <div class="line">12/40 Cedar Court</div>
      <div class="line">Oregon - 987654321</div>
    </address>

    <div class="date">Date : 01 July 2018</div>

    <section class="body-copy">
      <p>Lorem ipsum dolor sit amet, justo platonem in per, dicant constituto ne eam. Aeque persecuti sit ea, at vis commodo tractatos vituperata, sea an albucius forensibus. Wisi quodsi id qui, duo tempor aliquam assentior eu, no diceret tibique definiebas mei. Id nec noster facilisi mandamus.</p>
      <p>Nullam definiebas signiferumque pro te, vel mutat lobortis conceptam in. Usu justo minimum an, ne regione sanctus praesent usu, eam ut adipisci volutpat. Vel odio tibique consequat ne, in dicit gubergren appellantur vis, quo ei omnis elitr. Qui ne enim dictas dissentiet, pro nulla quodsi deseruisse te. Vide prima eloquentiam pro ei, agam dicta in pro, eu persius propriae constituam sea. Ius ut iriure oblique laboramus, cu sed fugit commune invenire, viris repudiandae ex vis. Nullam definiebas signiferumque pro te, vel mutat lobortis conceptam in. Usu justo minimum an, ne regione sanctus praesent usu, eam ut adipisci volutpat. Vel odio tibique consequat ne, in dicit gubergren appellantur vis, quo ei omnis elitr. Qui ne enim dictas dissentiet, pro nulla quodsi deseruisse te. Vide prima eloquentiam pro ei, agam dicta in pro, eu persius propriae constituam sea. Ius ut iriure oblique laboramus, cu sed fugit commune invenire, viris repudiandae ex vis. Nullam definiebas signiferumque pro te, vel mutat lobortis conceptam in. Usu justo minimum an, ne regione sanctus praesent usu, eam ut adipisci volutpat. Vel odio tibique consequat ne, in dicit gubergren appellantur vis, quo ei omnis elitr. Qui ne enim dictas dissentiet, pro nulla quodsi deseruisse te. Vide prima eloquentiam pro ei, agam dicta in pro, eu persius propriae constituam sea. Ius ut iriure oblique laboramus, cu sed fugit commune invenire, viris repudiandae ex vis.</p>
    </section>

    <footer class="footer">
      <div class="address"><strong>Velk Consulting</strong> - 214 N Linden Avenue, Carver, OR 97015</div>
      <div class="contact-row">
        <span class="contact-item">
          <svg viewBox="0 0 16 16" aria-hidden="true"><path d="M3.5 1.5l2.5 0 1 3.5-1.7 1.2c.9 1.9 2.4 3.4 4.3 4.3L10.8 8.8l3.5 1v2.6c0 .9-.8 1.6-1.7 1.6C7 13.5 2 8.5 2 3.2 2 2.3 2.6 1.5 3.5 1.5z" fill="var(--gold)"/></svg>
          000 000 0000
        </span>
        <span class="contact-item">
          <svg viewBox="0 0 16 16" aria-hidden="true"><rect x="1.5" y="3.5" width="13" height="9" fill="none" stroke="var(--gold)" stroke-width="1.2"/><path d="M1.5 3.5L8 9l6.5-5.5" fill="none" stroke="var(--gold)" stroke-width="1.2"/></svg>
          info@velkconsulting.com
        </span>
        <span class="contact-item">
          <svg viewBox="0 0 16 16" aria-hidden="true"><g fill="none" stroke="var(--gold)" stroke-width="1"><circle cx="8" cy="8" r="6.3"/><ellipse cx="8" cy="8" rx="2.8" ry="6.3"/><path d="M1.7 8h12.6M2.6 4.8h10.8M2.6 11.2h10.8"/></g></svg>
          www.velkconsulting.com
        </span>
      </div>
    </footer>
  </main>
</body>
</html>
```